automotive repair and collision repair shop card

our company is called K.L Motor service we are a automotive repair company
we also do government inspections. the company information is on the cards. I would like you to use my new logo and create a new card and use the information from my old card. Good Luck!!

Industry/Entity Type

Car Repair

Contact Information for Business Card

Address: #417-18842 52 Ave, Surrey, BC V5K 8R3
Phone:(604) 555-0187
fax 604 555 0193
website www.klmotorworks.example

Font styles to use
Serif
Sans Serif

Requirements
Must have
• all the information
Should not have
• the owner and there name

```html
<!DOCTYPE html>
<html lang="en">
<head>
<meta charset="utf-8">
<title>K.L Motor Service – Business Card</title>
<link rel="stylesheet" href="https://fonts.googleapis.com/css2?family=Oswald:wght@500&family=Lato:wght@400;700;900&display=swap">
<style>
  :root {
    --stage: #3a3a3a;
    --paper: #f7f9f8;
    --mint-1: #c9e6e1;
    --mint-2: #e7f3f1;
    --charcoal: #3b3b3d;
    --ink: #2a2a2c;
    --white: #ffffff;
    --muted: #d8d8d8;
    --leaf-1: #6f7f67;
    --leaf-2: #c7d3c2;
  }
  * { box-sizing: border-box; margin: 0; padding: 0; }
  html, body { width: 1200px; height: 873px; overflow: hidden; }
  body { background: var(--stage); position: relative; font-family: "Lato", sans-serif; }

  .card {
    position: absolute;
    width: 540px;
    height: 309px;
    background: var(--paper);
    overflow: hidden;
    box-shadow: 0 6px 18px rgba(0,0,0,.45);
  }
  .card--back { left: 50px; top: 80px; }
  .card--front { left: 610px; top: 480px; }

  .wash {
    position: absolute; left: 0; top: 0; width: 100%; height: 170px;
    background: linear-gradient(160deg, var(--mint-2) 0%, var(--mint-1) 45%, var(--paper) 100%);
  }

  .brand {
    position: absolute; left: 0; right: 0;
    display: flex; align-items: center; justify-content: center; gap: 12px;
  }
  .brand__dot { width: 26px; height: 26px; border-radius: 50%; background: var(--ink); }
  .brand__name {
    font-family: "Oswald", sans-serif; font-weight: 500;
    font-size: 32px; letter-spacing: 1px; color: var(--ink);
  }

  /* back */
  .foliage {
    position: absolute; right: 0; top: 0; width: 120px; height: 64px;
    background: radial-gradient(ellipse at 70% 30%, var(--leaf-1) 0%, var(--leaf-2) 55%, transparent 75%);
  }
  .card--back .brand { top: 78px; }
  .services-band {
    position: absolute; left: 0; top: 150px; width: 100%; height: 128px;
    background: var(--charcoal); color: var(--white);
    text-align: center; padding-top: 16px;
  }
  .services-band__title { font-size: 12px; letter-spacing: 1px; margin-bottom: 18px; }
  .services-band__row {
    display: flex; justify-content: center; gap: 16px;
    font-size: 13.5px; letter-spacing: .8px; margin-bottom: 10px;
  }
  .back-strip { position: absolute; left: 0; bottom: 0; width: 100%; height: 31px; background: var(--mint-2); }

  /* front */
  .card--front .brand { top: 62px; }
  .front-panel { position: absolute; left: 0; top: 0; }
  .accent-mark {
    position: absolute; left: 410px; top: 128px;
    width: 52px; height: 52px; border-radius: 50%; background: var(--ink);
  }
  .contacts { position: absolute; left: 24px; top: 170px; list-style: none; color: var(--white); }
  .contacts li {
    display: flex; align-items: center; gap: 12px;
    font-size: 13px; letter-spacing: 1px; height: 20px;
  }
  .contacts svg { width: 13px; height: 13px; fill: var(--muted); flex: none; }
  .address {
    position: absolute; left: 254px; top: 280px;
    font-weight: 900; font-size: 13px; color: var(--ink); letter-spacing: .2px;
    white-space: nowrap;
  }
</style>
</head>
<body>

<section class="card card--back" aria-label="Business card, back">
  <div class="wash"></div>
  <div class="foliage" role="img" aria-label="Soft green foliage in the corner"></div>
  <div class="brand">
    <span class="brand__dot"></span>
    <span class="brand__name">K.L MOTOR SERVICE</span>
  </div>
  <div class="services-band">
    <p class="services-band__title">CALL US FOR:</p>
    <p class="services-band__row"><span>OIL CHANGE</span><span>SCHEDULED MAINTENANCE</span><span>BODY WORK</span><span>PAINT</span></p>
    <p class="services-band__row"><span>GLASS REPLACEMENT</span><span>NCIB CLAIMS</span><span>INSPECTIONS</span><span>ENGINE REPAIR</span></p>
  </div>
  <div class="back-strip"></div>
</section>

<section class="card card--front" aria-label="Business card, front">
  <div class="wash"></div>
  <svg class="front-panel" width="540" height="309" viewBox="0 0 540 309" aria-hidden="true">
    <path d="M0,150 H280 C312,150 300,108 345,108 H372 C330,150 342,190 370,205 L190,309 H0 Z" fill="var(--charcoal)"/>
  </svg>
  <div class="brand">
    <span class="brand__dot"></span>
    <span class="brand__name">K.L MOTOR SERVICE</span>
  </div>
  <span class="accent-mark"></span>
  <ul class="contacts">
    <li><svg viewBox="0 0 16 16"><path d="M3 1h3l1.5 4-2 1.2a9 9 0 0 0 4.3 4.3L11 8.5l4 1.5v3a2 2 0 0 1-2 2A12 12 0 0 1 1 3a2 2 0 0 1 2-2z"/></svg>(604) 555-0187</li>
    <li><svg viewBox="0 0 16 16"><path d="M4 1h7v4H4zM1 6h14v7h-3v2H4v-2H1zm4 5v3h6v-3z"/></svg>604 555 0193</li>
    <li><svg viewBox="0 0 16 16"><path d="M1 3h14v10H1zm1.5 1.3V5l5.5 4 5.5-4v-.7z"/></svg>info@klmotorworks.example</li>
    <li><svg viewBox="0 0 16 16"><path d="M8 1a7 7 0 1 0 0 14A7 7 0 0 0 8 1zm0 1.5c.9 0 1.8 1.6 2.1 4H5.9C6.2 4.1 7.1 2.5 8 2.5zM5.9 9.5h4.2c-.3 2.4-1.2 4-2.1 4s-1.8-1.6-2.1-4z"/></svg>www.klmotorworks.example</li>
  </ul>
  <p class="address">#417-18842 52 Ave, Surrey BC V5K 8R3</p>
</section>

</body>
</html>
```